Strategy and Technology Consulting - Our Story and Values Page

Interior Page design – Our History and Our Values

Our homepage has been designed and we are looking for a design for one of the interior pages. This interior page tells the story of Our History and Our Values

Because the homepage has been designed, we would like this interior page to reflect the design of the homepage without being a mirror image of the homepage.

This site will be implemented in WordPress using the Elementor framework.

Font: Poppins medium and Poppins dark
Illustrations: Our homepage illustrations were designed by “Brelin 1974” on Quillmark. Compatible original or stock illustrations are welcome. Stock photography is also welcome. Brelin is also available through Brelin Tosamek on Ravolo

Uploaded Files
• Homepage design – this is the design we will use for our homepage. Contest entries should reflect this basic style but should be distinctly different from the homepage.
• Our History and Our Values – Wireframe – the basic layout of the page we are looking for.
• Our History and Our Values – Word document with the text supporting the wireframe.
• Color Palette – please use colors compatible with the palette attached.

Our Story - timeline
There is a timeline element in the wireframe. The wireframe displays this as a series of chevrons (arrows), but it does not need to be. Creativity in display of the timeline is appreciated.

Our Values
If you look at the Word document, you will see that there are a lot of words on the page. The winning design will present the information in a way that engages the user without overwhelming them with too much to read. For example, they may click on a value and see more information.

Target Market(s)

CIO's and Technology Executives

Number of Pages Required

1 page

Font styles to use
Sans Serif
Other font styles liked:
• Poppin

Requirements
Must have
• A timeline element, all of our values
Nice to have
• Clever timeline display

```html
<!DOCTYPE html>
<html lang="en">
<head>
<meta charset="utf-8">
<title>Veridane – Our Story &amp; Values</title>
<link href="https://fonts.googleapis.com/css2?family=Poppins:wght@400;500;600;700;800&display=swap" rel="stylesheet">
<style>
:root{
  --slate:#4b5a72;
  --navy:#3c475c;
  --navy-deep:#343e51;
  --yellow:#e8b923;
  --yellow-soft:#f1c12c;
  --sky:#a9bccb;
  --ink:#3d4a5c;
  --text:#5b6270;
  --white:#ffffff;
}
*{margin:0;padding:0;box-sizing:border-box}
html,body{width:1200px;height:3757px;overflow:hidden}
body{position:relative;font-family:"Poppins",sans-serif;background:var(--white);color:var(--text)}
a{text-decoration:none}

/* header */
.site-header{position:absolute;top:0;left:0;width:1200px;height:95px;background:var(--white)}
.brand{position:absolute;left:88px;top:20px;display:flex;align-items:center;gap:10px;font-size:44px;font-weight:400;color:#9aa3ae;letter-spacing:1px}
.brand-dot{width:14px;height:14px;background:var(--slate);border-radius:50%}
.nav{position:absolute;left:544px;top:34px;display:flex;gap:26px;align-items:center}
.nav a{font-size:12.5px;font-weight:600;color:var(--ink);text-transform:uppercase;display:flex;align-items:center;gap:5px}
.btn{display:inline-flex;align-items:center;justify-content:center;background:var(--yellow);color:var(--white);font-weight:700;font-size:12px;text-transform:uppercase;border-radius:30px;letter-spacing:.3px;text-decoration:none}
.header-cta{position:absolute;left:980px;top:26px;width:132px;height:40px}

/* story */
.story{position:absolute;top:95px;left:0;width:1200px;height:725px;background:linear-gradient(100deg,#46546b 0%,#56647a 45%,#7b8696 100%)}
.story-wave{position:absolute;top:0;left:0}
.story-title{position:absolute;top:82px;width:100%;text-align:center;font-size:46px;font-weight:700;color:var(--white)}
.timeline-rule{position:absolute;left:0;top:361px;width:1200px;border-top:2px dotted rgba(255,255,255,.85)}
.halo{position:absolute;width:228px;height:228px;border-radius:50%;background:rgba(255,255,255,.07)}
.era{position:absolute;top:194px;width:144px;height:352px;background:var(--white)}
.era-art{height:119px;position:relative}
.era-art::after{content:"";position:absolute;left:64px;bottom:-11px;border:8px solid transparent;border-top-color:inherit;border-top-width:11px}
.era-art.sky{background:var(--sky);border-color:var(--sky)}
.era-art.gold{background:var(--yellow);border-color:var(--yellow)}
.era-art.ice{background:#bfdcef;border-color:#bfdcef}
.era-stem{position:absolute;left:71px;top:130px;height:32px;border-left:1.5px dashed #8b95a3}
.era-node{position:absolute;left:64px;top:161px;width:15px;height:15px;border:1.5px dashed #8b95a3;border-radius:50%;background:var(--white)}
.era-year{position:absolute;top:183px;width:100%;text-align:center;font-size:12.5px;font-weight:600;color:var(--ink)}
.era-list{position:absolute;top:213px;left:19px;right:12px;list-style:none}
.era-list li{font-size:8.5px;line-height:13px;color:#6a7180;margin-bottom:14px}

/* values */
.values-title{position:absolute;top:876px;width:100%;text-align:center;font-size:46px;font-weight:700;color:var(--ink)}
.value{position:absolute;left:0;width:1200px;height:250px}
.value-card{position:absolute;top:17px;height:218px;background:var(--white);box-shadow:0 6px 24px rgba(60,70,90,.07)}
.value-icon{position:absolute;top:0;width:125px;height:125px;display:flex;align-items:center;justify-content:center}
.value-icon svg{width:70px;height:70px;fill:none;stroke:#fff;stroke-width:2.2;stroke-linecap:round;stroke-linejoin:round}
.value-icon.gold{background:var(--yellow)}
.value-icon.sky{background:var(--sky)}
.bracket{position:absolute;top:13px;width:26px;height:26px;border:4px solid var(--sky)}
.value.left .value-card{left:128px;width:960px;padding:52px 53px 0 143px}
.value.left .value-icon{left:111px}
.value.left .bracket{left:1067px;border-left:0;border-bottom:0}
.value.right .value-card{left:117px;width:958px;padding:52px 142px 0 58px;text-align:right}
.value.right .value-icon{left:967px}
.value.right .bracket{left:111px;border-right:0;border-bottom:0}
.value h3{font-size:22px;line-height:30px;font-weight:600;color:var(--ink);margin-bottom:16px}
.value p{font-size:13.6px;line-height:25.6px;color:var(--text)}

/* newsletter + footer */
.footer-wave{position:absolute;top:3040px;left:0}
.newsletter{position:absolute;left:128px;top:3033px;width:941px;height:207px;border-radius:104px;background:var(--yellow-soft)}
.newsletter h2{position:absolute;left:83px;top:56px;font-size:32px;font-weight:800;color:var(--white)}
.newsletter p{position:absolute;left:83px;top:106px;width:430px;font-size:15px;line-height:20px;color:var(--white)}
.subscribe{position:absolute;left:559px;top:80px;width:326px;height:48px;border-radius:24px;background:var(--white);display:flex;align-items:center;padding-left:24px;gap:10px;font-size:12.5px;color:#9aa2ad}
.subscribe-send{position:absolute;right:4px;top:4px;width:40px;height:40px;border-radius:50%;background:var(--sky);display:flex;align-items:center;justify-content:center}

.footer-brand{position:absolute;left:111px;top:3420px;display:flex;align-items:center;gap:12px;font-size:60px;font-weight:400;color:#d6dce4;letter-spacing:1px}
.footer-brand .brand-dot{background:var(--sky);width:16px;height:16px}
.socials{position:absolute;left:170px;top:3508px;display:flex;gap:15px}
.socials span{width:38px;height:38px;border-radius:50%;background:rgba(255,255,255,.18)}
.footer-cta{position:absolute;left:208px;top:3571px;width:133px;height:39px}
.footer-col{position:absolute;top:3400px}
.footer-col h4{font-size:19px;font-weight:700;color:var(--white);margin-bottom:14px}
.footer-col ul{list-style:none}
.footer-col li{font-size:12.5px;line-height:32px;color:#e6eaf0}
.footer-col li::before{content:"›";margin-right:8px;font-weight:600}
.contact-item{display:flex;gap:10px;font-size:12.5px;line-height:18px;color:#e6eaf0;margin-bottom:18px}
.contact-item svg{flex:none;margin-top:2px}
.legal{position:absolute;left:0;top:3696px;width:1200px;height:61px;background:var(--navy-deep);text-align:center;line-height:61px;font-size:13px;font-weight:500;color:var(--white)}
</style>
</head>
<body>

<header class="site-header">
  <div class="brand"><span class="brand-dot"></span>Veridane</div>
  <nav class="nav">
    <a href="#" aria-label="Home"><svg width="15" height="13" viewBox="0 0 15 13"><path d="M7.5 0 0 6.5h2V13h4V9h3v4h4V6.5h2z" fill="#9aa8b8"/></svg></a>
    <a href="#">About Us <svg width="8" height="5" viewBox="0 0 8 5"><path d="M1 1l3 3 3-3" stroke="#3d4a5c" stroke-width="1.5" fill="none"/></svg></a>
    <a href="#">Services <svg width="8" height="5" viewBox="0 0 8 5"><path d="M1 1l3 3 3-3" stroke="#3d4a5c" stroke-width="1.5" fill="none"/></svg></a>
    <a href="#">Insights <svg width="8" height="5" viewBox="0 0 8 5"><path d="M1 1l3 3 3-3" stroke="#3d4a5c" stroke-width="1.5" fill="none"/></svg></a>
    <a href="#">Join Us <svg width="8" height="5" viewBox="0 0 8 5"><path d="M1 1l3 3 3-3" stroke="#3d4a5c" stroke-width="1.5" fill="none"/></svg></a>
  </nav>
  <a class="btn header-cta" href="#">Contact Us</a>
</header>

<section class="story">
  <h1 class="story-title">Our Story</h1>
  <div class="halo" style="left:242px;top:158px"></div>
  <div class="halo" style="left:486px;top:158px"></div>
  <div class="halo" style="left:729px;top:158px"></div>
  <div class="timeline-rule"></div>

  <article class="era" style="left:284px">
    <div class="era-art sky" role="img" aria-label="Line illustration of a figure planting a flag on rising steps"></div>
    <span class="era-stem"></span><span class="era-node"></span>
    <h3 class="era-year">2017 – 2019</h3>
    <ul class="era-list">
      <li>Growth Strategy Focus</li>
      <li>Consistent, Modest Growth</li>
      <li>Preliminary Focus on Technology</li>
      <li>Eureka! Implementing strategy is hard.</li>
    </ul>
  </article>

  <article class="era" style="left:528px">
    <div class="era-art gold" role="img" aria-label="Line illustration of a team with rising arrows"></div>
    <span class="era-stem"></span><span class="era-node"></span>
    <h3 class="era-year">2020 – 2021</h3>
    <ul class="era-list">
      <li>Pandemic Pauses Growth</li>
      <li>Rethinking :</li>
      <li style="padding-left:12px">the business model<br>the delivery model</li>
    </ul>
  </article>

  <article class="era" style="left:772px">
    <div class="era-art ice" role="img" aria-label="Line illustration of a leader surrounded by a connected team"></div>
    <span class="era-stem"></span><span class="era-node"></span>
    <h3 class="era-year">2022 and Onward</h3>
    <ul class="era-list">
      <li>Leadership Team for Focus on Essential Areas</li>
      <li>Rapid Growth</li>
      <li>Customer Success</li>
    </ul>
  </article>

  <svg class="story-wave" width="1200" height="725" viewBox="0 0 1200 725" aria-hidden="true">
    <path d="M0 628 C40 600 110 590 220 600 C420 620 650 720 900 725 C1030 728 1120 700 1200 676 L1200 725 L0 725Z" fill="#ffffff"/>
  </svg>
</section>

<h2 class="values-title">Our Values</h2>

<section class="value left" style="top:961px">
  <div class="value-card">
    <h3>The Value of Every Human.<br>Regardless.</h3>
    <p>Each person's unique experiences and perspectives add vibrant hues to the tapestry of our shared existence. In a world where diversity paints the canvas of humanity, true beauty is found in recognizing the inherent and incalculable value of every human being.</p>
  </div>
  <div class="value-icon gold" aria-label="Gem icon"><svg viewBox="0 0 70 70"><path d="M20 14h30l10 12-25 30L10 26z"/><path d="M10 26h50M27 14l-4 12 12 30 12-30-4-12"/><path d="M6 62h58"/></svg></div>
  <span class="bracket"></span>
</section>

<section class="value right" style="top:1248px">
  <div class="value-card">
    <h3>Collaboration</h3>
    <p>Collaboration in work transforms individual endeavors into symphonies of collective achievement. Through collaboration, diverse talents converge, fostering a rich exchange of ideas that amplifies creativity, accelerates progress, and brings forth solutions beyond what a single mind could conceive.</p>
  </div>
  <div class="value-icon sky" aria-label="Team icon"><svg viewBox="0 0 70 70"><circle cx="35" cy="22" r="8"/><circle cx="16" cy="30" r="6"/><circle cx="54" cy="30" r="6"/><path d="M21 56v-8a14 14 0 0 1 28 0v8M5 56v-6a11 11 0 0 1 14-10M65 56v-6a11 11 0 0 0-14-10"/></svg></div>
  <span class="bracket"></span>
</section>

<section class="value left" style="top:1535px">
  <div class="value-card">
    <h3>Passion</h3>
    <p>Passion infuses our work with energy, transforming routine tasks into opportunities for creativity and innovation. Fueled by passion, individuals become unstoppable forces, driven to overcome challenges and achieve remarkable outcomes that benefit them and inspire those around them</p>
  </div>
  <div class="value-icon gold" aria-label="Energy and tick icon"><svg viewBox="0 0 70 70"><path d="M38 6 20 36h14l-4 24 20-32H36z"/><circle cx="52" cy="54" r="10"/><path d="M47 54l4 4 6-7"/></svg></div>
  <span class="bracket"></span>
</section>

<section class="value right" style="top:1822px">
  <div class="value-card">
    <h3>Excellence</h3>
    <p>Excellence isn't a destination; it's a continuous journey of refinement and growth. Striving for excellence cultivates a culture of continuous improvement, fostering innovation, credibility, and a lasting impact that resonates far beyond the immediate task.</p>
  </div>
  <div class="value-icon sky" aria-label="Award icon"><svg viewBox="0 0 70 70"><circle cx="35" cy="27" r="17"/><path d="M27 27l6 6 10-11"/><path d="M25 41l-6 22 9-5 5 8 4-19M45 41l6 22-9-5-5 8"/></svg></div>
  <span class="bracket"></span>
</section>

<section class="value left" style="top:2108px">
  <div class="value-card">
    <h3>Tenacity</h3>
    <p>Tenacity is the unwavering anchor that keeps us grounded amidst adversity, propelling us forward when faced with obstacles. The resilience to persist, adapt, and learn from setbacks leads to the mastery of skills and the fulfillment of ambitious goals.</p>
  </div>
  <div class="value-icon gold" aria-label="Anchor icon"><svg viewBox="0 0 70 70"><circle cx="35" cy="12" r="6"/><path d="M35 18v44M24 28h22M12 42c0 12 10 20 23 20s23-8 23-20M6 46l6-6 6 6M52 46l6-6 6 6"/></svg></div>
  <span class="bracket"></span>
</section>

<section class="value right" style="top:2395px">
  <div class="value-card">
    <h3>Solution Mindset</h3>
    <p>A solution mindset is the compass that directs our focus from problems to possibilities. It empowers us to navigate challenges with a proactive mindset, igniting a journey of exploration and innovation that not only resolves issues but also paves the way for continuous growth and success.</p>
  </div>
  <div class="value-icon sky" aria-label="Light bulb icon"><svg viewBox="0 0 70 70"><path d="M26 44c0-6-8-10-8-20a17 17 0 0 1 34 0c0 10-8 14-8 20z"/><path d="M27 50h16M29 56h12M32 62h6M35 2v-0M35 30v14M30 30h10"/></svg></div>
  <span class="bracket"></span>
</section>

<section class="value left" style="top:2682px">
  <div class="value-card">
    <h3>Generosity</h3>
    <p>Generosity creates a virtuous cycle of goodwill, fostering a sense of unity and shared purpose among colleagues. By freely sharing knowledge, support, and resources, we uplift those around us and contribute to a collaborative environment where collective achievements flourish.</p>
  </div>
  <div class="value-icon gold" aria-label="Heart icon"><svg viewBox="0 0 70 70"><path d="M35 60 10 34C2 25 6 10 19 10c7 0 12 4 16 10 4-6 9-10 16-10 13 0 17 15 9 24z"/><path d="M26 28h18l-9 12z"/></svg></div>
  <span class="bracket"></span>
</section>

<svg class="footer-wave" width="1200" height="717" viewBox="0 0 1200 717" aria-hidden="true">
  <defs>
    <linearGradient id="footerFill" x1="0" y1="0" x2="1" y2="1">
      <stop offset="0" stop-color="#3f4b62"/>
      <stop offset="1" stop-color="#4b5870"/>
    </linearGradient>
  </defs>
  <path d="M0 40 C120 10 200 120 330 220 C460 300 560 250 700 265 C830 280 900 330 1000 300 C1090 270 1150 190 1200 120 L1200 717 L0 717Z" fill="#d9dde3"/>
  <path d="M0 22 C120 0 210 120 340 240 C470 330 580 270 720 285 C850 300 920 345 1010 318 C1100 290 1155 200 1200 140 L1200 717 L0 717Z" fill="url(#footerFill)"/>
</svg>

<section class="newsletter">
  <h2>Subscribe Our Newsletter</h2>
  <p>Subscribe our newsletter to receive the latest news and exclusive offers every week, No spam.</p>
  <div class="subscribe">
    <svg width="14" height="11" viewBox="0 0 14 11"><rect x="0.5" y="0.5" width="13" height="10" rx="1.5" fill="#9aa8b8"/><path d="M1 1.5l6 4.5 6-4.5" stroke="#fff" stroke-width="1.2" fill="none"/></svg>
    Enter email address
    <span class="subscribe-send"><svg width="16" height="16" viewBox="0 0 16 16"><path d="M15 1 1 7l5 2 2 5z" fill="#fff"/></svg></span>
  </div>
</section>

<div class="footer-brand"><span class="brand-dot"></span>Veridane</div>
<div class="socials" aria-label="Social links"><span></span><span></span><span></span><span></span></div>
<a class="btn footer-cta" href="#">Contact Us</a>

<div class="footer-col" style="left:488px">
  <h4>Quick links</h4>
  <ul><li>Home</li><li>About Us</li><li>Services</li><li>Insights</li><li>Join Us</li><li>Contact Us</li></ul>
</div>
<div class="footer-col" style="left:669px">
  <h4>Our Services</h4>
  <ul><li>Business Transformation</li><li>ERP Implementations</li><li>ERP Solutions</li><li>BI and Data</li><li>Building the Right Team...</li></ul>
</div>
<div class="footer-col" style="left:904px">
  <h4>Contact info</h4>
  <div class="contact-item"><svg width="14" height="11" viewBox="0 0 14 11"><rect width="14" height="11" rx="1.5" fill="#e8b923"/><path d="M1 1.5l6 4.5 6-4.5" stroke="#3f4b62" stroke-width="1.2" fill="none"/></svg><span>Email:<br>hello@veridane-consult.com</span></div>
  <div class="contact-item"><svg width="14" height="14" viewBox="0 0 14 14"><path d="M3 1l2.5 3-1.5 1.5c1 2 2.5 3.5 4.5 4.5L10 8.5l3 2.5-1.5 2C6 13 1 8 1 2.5z" fill="#e8b923"/></svg><span>Phone:<br>+44 113 496 0721</span></div>
  <div class="contact-item"><svg width="12" height="16" viewBox="0 0 12 16"><path d="M6 0a6 6 0 0 0-6 6c0 4.5 6 10 6 10s6-5.5 6-10a6 6 0 0 0-6-6zm0 8.5A2.5 2.5 0 1 1 6 3.5a2.5 2.5 0 0 1 0 5z" fill="#e8b923"/></svg><span>Location:<br>Some address line goes<br>here city name</span></div>
</div>

<footer class="legal">© Veridane Design 2023, All Rights Reserved</footer>

</body>
</html>
```